Trendy eye catching business card for lawn mowing business

Turf Tidy, a local community lawn mowing service, requires an eye catching trendy business card to drop into letterboxes.

We could simply throw something together from a Microsoft Word template, but we are wanting something more than this. Some other business’ images are attached for some inspiration.

We are requiring the card to have Turf Tidy with our slogan, Call The Brindles. In addition, provide details with that we are a local, affordable lawn mowing service, and for other gardening matters to simply just ask!
Plus the relevant contact details, phone, email, social media.

Target Market(s)

Local community members who require assistance with their garden care

Industry/Entity Type

Gardening

Contact Information for Business Card

the name TURF TIDY is our logo
telephone logo 0438 215 967
email logo turftidy@postbox-mail.example
Instagram logo turftidy
Facebook logo turftidy.sth
Lawn Mowing Service
Local Affordable
edge trim, blow and clipping removal included.
Other gardening matters, just ask!

Font styles to use
Serif
Sans Serif
Decorative
Script

Colors
9bcb3c
ffffff

Requirements
Must have
• All the details listed in Business Card Details.
Make these words prominent:
Turf Tidy
Lawn Mowing Service
Local
Affordable
Nice to have
• Our slogan ‘Call The Brindles’ incorporated.
Different colour background for front and reverse side
Greens, white and black colours
Subtle grass blades images incorporated
Should not have
• No images of lawnmowers.
No images of men/cartoons.
No using initials for Turf Tidy

```html
<!DOCTYPE html>
<html lang="en">
<head>
<meta charset="utf-8">
<title>Turf Tidy — Business Card</title>
<link rel="stylesheet" href="https://fonts.googleapis.com/css2?family=Archivo+Black&family=Quicksand:wght@500;700&display=swap">
<style>
  :root{
    --lawn:#9bcb3c;
    --white:#ffffff;
    --charcoal:#464646;
    --ink:#333333;
    --backdrop:#2a2a2a;
  }
  *{margin:0;padding:0;box-sizing:border-box}
  html,body{width:1200px;height:900px;overflow:hidden;background:var(--backdrop)}
  .sheet{width:1200px;height:900px;display:flex;flex-direction:column;align-items:center;justify-content:center;gap:36px}
  .card{position:relative;width:700px;height:400px;overflow:hidden}

  /* Front */
  .card--front{background:var(--lawn);color:var(--white);text-align:center;padding-top:48px}
  .card--front .edge-tab{position:absolute;width:10px;height:80px;background:var(--white)}
  .card--front .edge-tab--left{left:0;top:96px}
  .card--front .edge-tab--right{right:0;top:230px}
  .brand{display:inline-block;text-align:center}
  .brand__name{font-family:"Archivo Black",sans-serif;font-size:44px;letter-spacing:1px;line-height:1}
  .brand__rule{height:2px;margin:6px 0 4px}
  .brand__slogan{font-family:"Quicksand",sans-serif;font-weight:700;font-size:15px;letter-spacing:2px;text-transform:uppercase}
  .card--front .brand__rule{background:var(--white)}
  .offer{margin-top:30px;font-family:"Archivo Black",sans-serif;font-size:23px;line-height:1.05;text-transform:uppercase;letter-spacing:.5px}
  .extras{margin-top:28px;font-family:"Quicksand",sans-serif;font-weight:500;font-size:17px;line-height:1.4;color:var(--ink)}
  .extras span{display:block}

  /* Back */
  .card--back{background:var(--white)}
  .card--back .brand{position:absolute;left:38px;top:40px;text-align:left}
  .card--back .brand__name{color:var(--lawn)}
  .card--back .brand__rule{background:var(--charcoal)}
  .card--back .brand__slogan{color:var(--ink);padding-left:60px}
  .person{position:absolute;right:36px;top:118px;text-align:right;font-family:"Quicksand",sans-serif}
  .person__name{color:var(--lawn);font-weight:700;font-size:31px;letter-spacing:1px;text-transform:uppercase}
  .person__role{color:var(--ink);font-weight:500;font-size:17px}
  .swoosh{position:absolute;left:0;top:0;width:700px;height:400px}
  .contact{position:absolute;right:36px;bottom:30px;list-style:none;font-family:"Quicksand",sans-serif;font-weight:500;font-size:19px;color:var(--white);text-align:right}
  .contact li{display:flex;justify-content:flex-end;align-items:center;gap:14px;line-height:1.5}
  .contact .icon{width:20px;height:20px;flex:none}
  .contact .mark{width:18px;height:18px;border:2px solid var(--white);border-radius:4px;flex:none;margin:0 1px}
</style>
</head>
<body>
<main class="sheet">
  <section class="card card--front" aria-label="Card front">
    <span class="edge-tab edge-tab--left"></span>
    <span class="edge-tab edge-tab--right"></span>
    <div class="brand">
      <div class="brand__name">TURF TIDY</div>
      <div class="brand__rule"></div>
      <div class="brand__slogan">Call The Brindles</div>
    </div>
    <div class="offer">
      <div>Turf Tidy</div>
      <div>Lawn Mowing Service</div>
      <div>Local</div>
      <div>Affordable</div>
    </div>
    <p class="extras">
      <span>Edge trim, blow and clipping removal included.</span>
      <span>Other gardening matters, JUST ASK!</span>
    </p>
  </section>

  <section class="card card--back" aria-label="Card back">
    <svg class="swoosh" viewBox="0 0 700 400" aria-hidden="true">
      <path d="M0 262 C120 300 260 290 420 232 C540 190 640 186 700 190 L700 400 L0 400 Z" fill="var(--lawn)"/>
      <path d="M0 236 C110 262 240 262 400 212 C520 174 630 170 700 176 L700 196 C620 188 520 196 420 230 C270 282 130 290 0 262 Z" fill="var(--charcoal)"/>
      <path d="M0 248 C110 274 240 272 400 222 C520 186 630 182 700 188 L700 194 C630 190 520 198 410 232 C260 282 120 286 0 262 Z" fill="var(--white)"/>
    </svg>
    <div class="brand">
      <div class="brand__name">TURF TIDY</div>
      <div class="brand__rule"></div>
      <div class="brand__slogan">Call The Brindles</div>
    </div>
    <div class="person">
      <div class="person__name">Dalen Prior</div>
      <div class="person__role">Director/ Owner</div>
    </div>
    <ul class="contact">
      <li>0438 215 967
        <svg class="icon" viewBox="0 0 20 20" aria-hidden="true"><path d="M5 2 L8 2 L9 6 L7 8 C8 10 10 12 12 13 L14 11 L18 12 L18 15 C18 17 16 18 14 17 C8 15 4 11 3 6 C2 4 3 2 5 2 Z" fill="none" stroke="var(--white)" stroke-width="1.6" stroke-linejoin="round"/></svg>
      </li>
      <li>turftidy@postbox-mail.example
        <svg class="icon" viewBox="0 0 20 20" aria-hidden="true"><rect x="2" y="4" width="16" height="12" rx="1" fill="none" stroke="var(--white)" stroke-width="1.6"/><path d="M2 5 L10 11 L18 5" fill="none" stroke="var(--white)" stroke-width="1.6"/></svg>
      </li>
      <li>instagram.com/turftidy <span class="mark"></span></li>
      <li>fb.me/turftidy.com.au <span class="mark"></span></li>
    </ul>
  </section>
</main>
</body>
</html>
```